A new updated business card. A good first impression for new customers to our business.

I need something unique. I will attached a picture of our old rubbish cards, and also our current Logo ( I think this needs an update if you have any ideas, its very basic and budget)The best way you will get to see my business is checking our Facebook page, I don't really know what else to say, but anything you want to know, ask away.www.facebook.com/tkwashandseal/

Target Market(s)

Home owners

Industry/Entity Type

Business

Contact Information for Business Card

T&K's Pressure Cleaning & Concrete Sealing
Maya 0492 615 370 maya@tkwashandseal.com
Dylan 0431 528 906 dylan@tkwashandseal.com

FB: www.facebook.com/tkwashandseal/
Website: www.tkwashandseal.net (This is pretty rubbish- we don't really use it)

100% customer satisfaction guaranteed

All aspects of Hi-Pressure Cleaning
Sealing & Re-Sealing
Roof Cleaning
Colour sealing
Decorative coatings

Free no obligation quotes

Requirements
Must have
• NO OBLIGATION FREE quotes
• 100% Customer satisfaction guaranteed
• Can you please add both names, contact details and email address on one card.
• Dylan 0431 528 906
• dylan@tkwashandseal.com
• Maya 0492 615 370
• maya@tkwashandseal.com
• Please change the services:
• Hot/Cold Hi-Pressure Cleaning
• Sealing & Re-Sealing
• Roof Cleaning
• Colour Sealing
• Decorative Coatings
• Concrete Honing
• Thanks
Nice to have
• Something a bit different, something eye catching.l

```html
<!DOCTYPE html>
<html lang="en">
<head>
<meta charset="utf-8">
<title>T&amp;K's Pressure Cleaning &amp; Concrete Sealing – Business Card</title>
<link rel="stylesheet" href="https://fonts.googleapis.com/css2?family=Open+Sans:wght@400;600;700&display=swap">
<style>
  :root {
    --stage: #2e2e2f;
    --card: #050505;
    --card-edge: #1a1a1a;
    --ink: #ffffff;
    --accent-cyan: #4cc3f0;
    --accent-red: #e0252b;
    --divider: #2a2a2a;
    --seal: #1b6fc4;
  }
  * { box-sizing: border-box; margin: 0; padding: 0; }
  html, body {
    width: 1200px; height: 900px; overflow: hidden;
    background: var(--stage);
    font-family: "Open Sans", Arial, sans-serif;
    color: var(--ink);
  }
  .sheet {
    position: relative; width: 1200px; height: 900px;
    display: flex; align-items: center; justify-content: center; gap: 40px;
  }
  .card {
    position: relative; width: 540px; height: 310px;
    background: var(--card);
    border: 1px solid var(--card-edge);
    border-radius: 22px;
    overflow: hidden;
  }
  .brand-name {
    font-weight: 600; color: var(--ink);
    text-transform: uppercase; letter-spacing: 0.04em; line-height: 1.35;
  }

  /* Front */
  .card-front .brand-name {
    position: absolute; left: 30px; top: 150px; width: 225px;
    font-size: 18px;
  }
  .card-front .divider {
    position: absolute; left: 268px; top: 26px; bottom: 26px;
    width: 1px; background: var(--divider);
  }
  .contacts {
    position: absolute; left: 292px; top: 34px; right: 20px;
    list-style: none;
  }
  .contact-person { margin-bottom: 16px; }
  .contact-name {
    color: var(--accent-cyan); font-weight: 700; font-size: 18px; line-height: 1.2;
    margin-bottom: 4px;
  }
  .contact-line {
    display: flex; align-items: center; gap: 10px;
    font-size: 13.5px; line-height: 1.6;
  }
  .contact-line svg { width: 12px; height: 12px; flex: none; }
  .online { margin-top: 4px; }

  /* Back */
  .card-back .brand-name {
    position: absolute; left: 30px; top: 150px; width: 200px;
    font-size: 16px;
  }
  .services {
    position: absolute; left: 235px; top: 48px;
    list-style: none;
  }
  .services li {
    display: flex; align-items: center; gap: 10px;
    font-size: 14px; line-height: 1.85;
  }
  .services li::before {
    content: ""; width: 7px; height: 7px; border-radius: 50%;
    background: var(--accent-cyan); flex: none;
  }
  .guarantee {
    position: absolute; right: 22px; top: 96px; width: 96px;
    display: flex; flex-direction: column; align-items: center; gap: 8px;
  }
  .guarantee-seal {
    width: 64px; height: 64px; border-radius: 50%;
    background: var(--seal);
  }
  .guarantee-text {
    font-size: 11px; font-weight: 600; line-height: 1.3;
    text-align: center; color: var(--ink);
  }
</style>
</head>
<body>
<main class="sheet">

  <section class="card card-front" aria-label="Card front">
    <p class="brand-name">T&amp;K's Pressure Cleaning &amp; Concrete Sealing</p>
    <div class="divider"></div>
    <ul class="contacts">
      <li class="contact-person">
        <p class="contact-name">Maya</p>
        <p class="contact-line">
          <svg viewBox="0 0 12 12"><path fill="#e0252b" d="M2.4 0.8l2 2-1 1.4c.7 1.5 1.8 2.6 3.4 3.4l1.4-1 2 2-1.3 1.6C5.6 10 2 6.4 0.8 2.1z"/></svg>
          0492 615 370
        </p>
        <p class="contact-line">
          <svg viewBox="0 0 12 12"><rect x="0.5" y="2" width="11" height="8" rx="1" fill="#e0252b"/><path d="M1 2.6l5 3.8 5-3.8" stroke="#050505" stroke-width="1.2" fill="none"/></svg>
          maya@tkwashandseal.com
        </p>
      </li>
      <li class="contact-person">
        <p class="contact-name">Dylan</p>
        <p class="contact-line">
          <svg viewBox="0 0 12 12"><path fill="#e0252b" d="M2.4 0.8l2 2-1 1.4c.7 1.5 1.8 2.6 3.4 3.4l1.4-1 2 2-1.3 1.6C5.6 10 2 6.4 0.8 2.1z"/></svg>
          0431 528 906
        </p>
        <p class="contact-line">
          <svg viewBox="0 0 12 12"><rect x="0.5" y="2" width="11" height="8" rx="1" fill="#e0252b"/><path d="M1 2.6l5 3.8 5-3.8" stroke="#050505" stroke-width="1.2" fill="none"/></svg>
          dylan@tkwashandseal.com
        </p>
      </li>
      <li class="online">
        <p class="contact-line">
          <svg viewBox="0 0 12 12"><circle cx="6" cy="6" r="4.5" fill="#e0252b"/></svg>
          tkwashandseal
        </p>
        <p class="contact-line">
          <svg viewBox="0 0 12 12"><circle cx="6" cy="6" r="5" fill="#e0252b"/><path d="M1 6h10M6 1c-2.4 3-2.4 7 0 10M6 1c2.4 3 2.4 7 0 10" stroke="#050505" stroke-width="0.9" fill="none"/></svg>
          www.tkwashandseal.net
        </p>
      </li>
    </ul>
  </section>

  <section class="card card-back" aria-label="Card back">
    <p class="brand-name">T&amp;K's Pressure Cleaning &amp; Concrete Sealing</p>
    <ul class="services">
      <li>Hot/Cold Hi-Pressure Cleaning</li>
      <li>Sealing &amp; Re-Sealing</li>
      <li>Roof Cleaning</li>
      <li>Colour Sealing</li>
      <li>Decorative Coatings</li>
      <li>Concrete Honing</li>
    </ul>
    <div class="guarantee">
      <div class="guarantee-seal" role="img" aria-label="Satisfaction guarantee seal"></div>
      <p class="guarantee-text">100% Satisfaction Guaranteed</p>
    </div>
  </section>

</main>
</body>
</html>
```